Flyer for photo scanning business

Hello,
I need a flyer created for my business that would be suitable for print, to drop in letterboxes in my local community.

I would like the flyer to convey very simply the services I offer which is scanning negatives, slides and VHS tapes to digital files.
Hopefully it can make it look like an easy process, as people are often daunted by the task of sorting through old photos so they don't always get around to having them scanned.

I have a pinned facebook post that can be used by the designer to reference my services. Pricing does not need to be included on the flyer.
http://facebook.com/lanternvaultmedia

Target Market(s)

Parents & Grandparents

Requirements
Must have
• Must make my services look simple! Refer to pinned facebook post for detailed outline of my services.

I would like to flyer to point towards my contact details -
www.lanternvault.com
Miriam 0482 917 336

Colours in line with my logo/brand (uploaded to brief).
Nice to have
• Stock images of 35mm film negatives, 8mm film, VHS tapes, or Brightfane slides would be worth including. I have also uploaded a mockup of the USB sticks that I provide with digitised images.
Should not have
• no prices needed,

```html
<!DOCTYPE html>
<html lang="en">
<head>
<meta charset="utf-8">
<title>Lanternvault Media – Scanning Flyer</title>
<link rel="stylesheet" href="https://fonts.googleapis.com/css2?family=Bebas+Neue&family=Cinzel:wght@700&family=Mulish:wght@400&family=Montserrat:wght@500;600&family=Roboto:wght@700&display=swap">
<style>
  :root {
    --stage: #ececec;
    --ink-dark: #14161f;
    --paper-light: #eef3fa;
    --brand-blue: #4f71a5;
    --brand-blue-light: #86afdb;
    --panel-blue: #6c8ab8;
    --step-top: #86acd8;
    --step-bottom: #4b6ea3;
    --step-frame: #c8dbf0;
    --highlight: #fff22e;
    --white: #ffffff;
    --promise-bg: rgba(226, 230, 238, 0.88);
  }
  * { box-sizing: border-box; margin: 0; padding: 0; }
  html, body { width: 1116px; height: 1200px; overflow: hidden; background: var(--stage); }

  .flyer {
    position: absolute; left: 110px; top: 20px;
    width: 896px; height: 1160px;
    background: var(--paper-light);
    overflow: hidden;
    box-shadow: 0 4px 18px rgba(0,0,0,0.15);
  }

  .photo-film {
    position: absolute; left: 0; top: 0; width: 512px; height: 581px;
    background: radial-gradient(circle at 20% 60%, #5b5c63 0%, #2b2c34 40%, var(--ink-dark) 80%);
  }
  .photo-slides {
    position: absolute; left: 512px; top: 0; width: 384px; height: 581px;
    background: linear-gradient(135deg, #8fc3e6 0%, #f2d321 25%, #d8302c 50%, #3a3d46 72%, #8fc3e6 100%);
  }

  .headline {
    position: absolute; left: 73px; top: 36px;
    font-family: "Bebas Neue", sans-serif; font-weight: 400;
    font-size: 86px; line-height: 68px; color: var(--white);
    white-space: nowrap; letter-spacing: 0;
  }
  .headline .accent { color: var(--highlight); }

  .usb-panel {
    position: absolute; left: 36px; top: 581px; width: 370px; height: 381px;
    background: var(--panel-blue);
  }
  .usb-photo {
    position: absolute; left: 0; top: 147px; width: 370px; height: 234px;
    background: linear-gradient(160deg, #7c9bc6 0%, #9db6d8 50%, #6f8fbd 100%);
  }

  .promise {
    position: absolute; left: 71px; top: 403px; width: 301px; height: 325px;
    background: var(--promise-bg);
    text-align: center; padding-top: 36px;
    color: #111;
  }
  .promise .lead {
    font-family: "Mulish", sans-serif; font-size: 21px; line-height: 26px;
  }
  .promise .big {
    font-family: "Cinzel", serif; font-weight: 700;
    font-size: 31px; line-height: 39px;
  }

  .steps {
    position: absolute; left: 457px; top: 231px; width: 401px;
  }
  .step {
    position: relative;
    border: 5px solid var(--step-frame);
    background: linear-gradient(180deg, var(--step-top), var(--step-bottom));
    color: var(--white); text-align: center;
    padding: 36px 38px 0;
  }
  .step + .step { margin-top: 2px; }
  .step::after {
    content: ""; position: absolute; left: 50%; bottom: -22px;
    width: 40px; height: 22px; transform: translateX(-50%);
    background: var(--step-bottom);
    clip-path: polygon(0 0, 100% 0, 50% 100%);
    z-index: 2;
  }
  .step-01 { height: 202px; }
  .step-02 { height: 231px; }
  .step-03 { height: 293px; }
  .step h2 {
    font-family: "Montserrat", sans-serif; font-weight: 600;
    font-size: 28px; line-height: 34px; letter-spacing: 1px; margin-bottom: 10px;
  }
  .step p {
    font-family: "Mulish", sans-serif; font-size: 18px; line-height: 27px;
  }

  .contact-band {
    position: absolute; left: 0; top: 993px; width: 896px; height: 167px;
    background: linear-gradient(180deg, var(--brand-blue-light), var(--brand-blue));
  }
  .brand-card {
    position: absolute; left: 36px; top: 37px; width: 383px; height: 105px;
    background: var(--white); border-radius: 14px;
    display: flex; align-items: center; justify-content: center; gap: 14px;
  }
  .brand-dot {
    width: 44px; height: 44px; border-radius: 50%; background: var(--brand-blue);
  }
  .brand-name {
    font-family: "Montserrat", sans-serif; font-weight: 500;
    font-size: 24px; line-height: 28px; letter-spacing: 2px;
    color: var(--brand-blue);
  }
  .contact-details {
    position: absolute; left: 446px; top: 42px; width: 410px;
    text-align: center; color: var(--white);
    font-family: "Roboto", sans-serif; font-weight: 700;
    font-size: 33px; line-height: 44px;
  }
</style>
</head>
<body>
  <main class="flyer">
    <div class="photo-film" role="img" aria-label="Close-up of old film reels, negatives and VHS tape"></div>
    <div class="photo-slides" role="img" aria-label="Pile of colourful plastic photo slide frames"></div>

    <h1 class="headline">SCANNING<br>NEGATIVES,<br>SLIDES AND<br>VHS TAPES TO<br><span class="accent">DIGITAL FILES</span></h1>

    <div class="usb-panel">
      <div class="usb-photo" role="img" aria-label="Two branded swivel USB sticks holding the digitised files"></div>
    </div>

    <div class="promise">
      <p class="lead">I promise to</p>
      <p class="big">MAKE IT<br>VERY EASY</p>
      <p class="lead">for you to keep your</p>
      <p class="big">PRECIOUS<br>MEMORIES<br>FOREVER</p>
    </div>

    <section class="steps">
      <div class="step step-01">
        <h2>STEP 01</h2>
        <p>Find your old negatives or tapes and organise them as much or as little as you want.</p>
      </div>
      <div class="step step-02">
        <h2>STEP 02</h2>
        <p>Contact me here or email miriam@lanternvault.com and I will come and collect these from your home in the hills area.</p>
      </div>
      <div class="step step-03">
        <h2>STEP 03</h2>
        <p>Once completed (usually within a few days) I will drop back your box of memories with a USB stick containing high resolution JPEG files. Contactless payment will be processed when I arrive.</p>
      </div>
    </section>

    <footer class="contact-band">
      <div class="brand-card">
        <span class="brand-dot"></span>
        <span class="brand-name">LANTERNVAULT<br>MEDIA</span>
      </div>
      <div class="contact-details">
        <p>Miriam 0482 917 336</p>
        <p>www.lanternvault.com</p>
      </div>
    </footer>
  </main>
</body>
</html>
```